Email design required

We need a design for a paid B2B email campaign and facebook / retargeting banner ads that match the same style.

Website: http://pelmora.staging.hostvantry.com/
Campaign Name: KEX Weariness
Example: http://liftmarrowsites.com/kex-weariness/
- I made this over the weekend. It has the right words, but the style / layout needs to change

Size: 600 pixels wide, no limit on length

Formatting:
Format CSS inline only - This will ensure that size, font family, colour, line height, etc. will all remain the same once it is dropped into our newsletter sending software. See below as an

example,

Here's a mockup of

Target Market(s)

Canadian mortgage brokers

Industry/Entity Type

Campaign

Font styles to use
Sans Serif

Colors
3277b5

Requirements
Must have
• Text from my website example http://liftmarrowsites.com/kex-weariness/
• Otherwise, do whatever you think would look good.

```html
<!DOCTYPE html>
<html lang="en">
<head>
<meta charset="utf-8">
<title>KEX Weariness – Pelmora Email</title>
<link rel="stylesheet" href="https://fonts.googleapis.com/css2?family=Open+Sans:ital,wght@0,400;0,600;0,700;1,400&display=swap">
<style>
:root{
  --stage:#2b2b2b;
  --navy:#233558;
  --brand-blue:#3277b5;
  --logo-blue:#1f5fa8;
  --orange:#f7931e;
  --white:#ffffff;
  --header-bg:#f8f8f8;
  --ink:#222222;
  --muted:#777777;
  --soft:#ededed;
  --footer:#3e3c4b;
  --avatar:#555555;
}
*{box-sizing:border-box;margin:0;padding:0}
html,body{width:960px;height:1200px;overflow:hidden}
body{background:var(--stage);font-family:"Open Sans",Arial,sans-serif;position:relative}
.email{position:absolute;left:222px;top:82px;width:480px;background:var(--white)}
.section{position:relative;width:100%}

.site-header{height:59px;background:var(--header-bg);display:flex;align-items:center;justify-content:space-between;padding:0 29px 0 22px}
.brand{display:flex;align-items:center;gap:5px;color:var(--logo-blue);font-weight:600;font-size:21px;letter-spacing:-0.3px}
.brand-mark{width:14px;height:14px;background:var(--logo-blue)}
.nav-link{font-size:11px;color:#666}

.hero{height:282px;background:var(--navy);text-align:center;color:var(--white)}
.hero-title{position:absolute;left:0;right:0;top:6px;font-size:30px;font-weight:700}
.hero-art{position:absolute;left:174px;top:56px;width:144px;height:114px;background:linear-gradient(180deg,#2d4270,#233558);border-radius:4px}
.hero-offer{position:absolute;left:0;right:0;top:192px;font-size:12px;font-weight:600;line-height:16px}
.hero-offer .price{color:var(--orange)}
.btn{position:absolute;display:flex;flex-direction:column;align-items:center;justify-content:center;background:var(--orange);color:var(--white);font-weight:700;border-radius:40px}
.hero-btn{left:178px;top:236px;width:144px;height:34px;font-size:11px}

.band{height:39px;background:var(--brand-blue);color:var(--white);display:flex;align-items:center;justify-content:center;font-weight:700;font-size:13.5px}
.band-reviews{height:40px}

.reviews{height:135px}
.avatar{position:absolute;left:48px;top:13px;width:100px;height:100px;border-radius:50%;background:var(--avatar)}
.quote{position:absolute;left:198px;top:24px;width:252px;font-size:10.4px;line-height:16px;font-style:italic;color:var(--muted)}
.reviewer{position:absolute;left:198px;top:93px;font-size:10.4px;color:var(--muted);font-weight:600;letter-spacing:0.2px}

.compare{height:256px}
.col-head{position:absolute;top:22px;transform:translateX(-50%);white-space:nowrap}
.col-head.ours{left:238px}
.col-head.ours .brand{font-size:18px}
.col-head.theirs{left:386px;top:25px;font-size:11.5px;font-weight:700;color:var(--ink)}
.row{position:absolute;left:0;width:100%;height:16px;font-size:10.4px;line-height:16px}
.row .tick{position:absolute;left:36px;top:2px;width:12px;height:12px}
.row .label{position:absolute;left:60px;color:#555}
.row .ours{position:absolute;left:231px;transform:translateX(-50%);font-weight:700;color:#333;white-space:nowrap}
.row .theirs{position:absolute;left:382px;transform:translateX(-50%);color:#666;white-space:nowrap}
.cta-btn{left:113px;top:179px;width:254px;height:60px}
.cta-btn .main{font-size:17.6px;letter-spacing:0.5px;line-height:22px}
.cta-btn .sub{font-size:11px;letter-spacing:0.5px;line-height:15px}

.about{height:192px;display:flex}
.about-photo{width:240px;height:100%;background:linear-gradient(160deg,#4a6aa0,#2c4678 60%,#223a66)}
.about-copy{width:240px;height:100%;background:var(--soft);padding:20px 22px 0 24px}
.about-title{font-size:14.4px;color:#333;margin-bottom:14px}
.about-body{font-size:10.4px;line-height:16px;color:#777}

.site-footer{height:38px;background:var(--footer);color:var(--white);display:flex;align-items:center;justify-content:space-between;padding:0 26px 0 23px;font-size:10.4px}
</style>
</head>
<body>
<main class="email">
  <header class="section site-header">
    <div class="brand"><span class="brand-mark"></span>Pelmora</div>
    <span class="nav-link">Contact</span>
  </header>

  <section class="section hero">
    <h1 class="hero-title">Experiencing KEX Weariness?</h1>
    <div class="hero-art" role="img" aria-label="Illustration of a tired worker slumped at a desk"></div>
    <p class="hero-offer">Unlimited Notice of Assessment Orders<br>For Just <span class="price">$29 / Month</span></p>
    <a class="btn hero-btn">Get Started Now</a>
  </section>

  <div class="section band band-reviews">Customer Reviews</div>

  <section class="section reviews">
    <div class="avatar" role="img" aria-label="Customer profile placeholder"></div>
    <p class="quote">I've used a few different services for this and Pelmora is by far the best. Fraction of the cost and I have the required docs within a couple of hours at most. Makes my life so much easier.</p>
    <p class="reviewer">Dale Marsh, BRX Calgary</p>
  </section>

  <div class="section band">Compare KEX Services</div>

  <section class="section compare">
    <div class="col-head ours"><div class="brand"><span class="brand-mark"></span>Pelmora</div></div>
    <div class="col-head theirs">‘Other Guys’</div>

    <div class="row" style="top:66px">
      <svg class="tick" viewBox="0 0 12 12"><circle cx="6" cy="6" r="4.5" fill="none" stroke="#555" stroke-width="1.4"/><path d="M3.6 6l2 2 4.8-5" fill="none" stroke="#555" stroke-width="1.6"/></svg>
      <span class="label">Price</span><span class="ours">$29 / month</span><span class="theirs">$39 / Order</span>
    </div>
    <div class="row" style="top:94px">
      <svg class="tick" viewBox="0 0 12 12"><circle cx="6" cy="6" r="4.5" fill="none" stroke="#555" stroke-width="1.4"/><path d="M3.6 6l2 2 4.8-5" fill="none" stroke="#555" stroke-width="1.6"/></svg>
      <span class="label">Units</span><span class="ours">Unlimited</span><span class="theirs">Just One</span>
    </div>
    <div class="row" style="top:121px">
      <svg class="tick" viewBox="0 0 12 12"><circle cx="6" cy="6" r="4.5" fill="none" stroke="#555" stroke-width="1.4"/><path d="M3.6 6l2 2 4.8-5" fill="none" stroke="#555" stroke-width="1.6"/></svg>
      <span class="label">Turnaround</span><span class="ours">4 Hours</span><span class="theirs">1 Day</span>
    </div>
    <div class="row" style="top:148px">
      <svg class="tick" viewBox="0 0 12 12"><circle cx="6" cy="6" r="4.5" fill="none" stroke="#555" stroke-width="1.4"/><path d="M3.6 6l2 2 4.8-5" fill="none" stroke="#555" stroke-width="1.6"/></svg>
      <span class="label">Other Services</span><span class="ours">Several</span><span class="theirs">X</span>
    </div>

    <a class="btn cta-btn"><span class="main">GET STARTED NOW</span><span class="sub">30-Day Money Back Guarantee</span></a>
  </section>

  <section class="section about">
    <div class="about-photo" role="img" aria-label="Photo of office filing cabinets in blue tones"></div>
    <div class="about-copy">
      <h2 class="about-title">About Us</h2>
      <p class="about-body">Pelmora provides on-demand administrative support for Mortgage Professionals across Canada. Everything from Notice of Assessment and Title Orders to inbound document sorting and lender fulfilment can be outsouced at a fraction of the cost of a full time administrator.</p>
    </div>
  </section>

  <footer class="section site-footer">
    <span>© Pelmora 2016 All rights reserved.</span>
    <span>Unsubscribe here</span>
  </footer>
</main>
</body>
</html>
```